Bram Keystone Homes needs a business card

We need a business card for a new company in Canada, Ontario. Our company is all about luxury contraction homes for our clients. Our product and services are custom projects design. Under the business logo that will be created, we want a slogan that will be a memorable phrase for consumers to remember us to tell their friends and relatives.

Additional infomation
- Ludovic Entrasse
- President / Ceo
-519.604.3087

Find point what luxury construction products and services can be done

We like to see colors:
- #663300
- and something other colors or color that would attract the client needs and wants

The final design should communicate leads from new or old clients that will grow our empire. Most of all, we try to work among the budget that clients want

NOTE
- we also need an icon for the business (Example: Instagram, Facebook, and Whatsapp icons)
- We want the company name to be remembered easily for clients and our distributors who would get our orders.
- we need an icon on the business cards: Facebook and Instagram.

Thanks,
Bram Keystone Homes

```html
<!DOCTYPE html>
<html lang="en">
<head>
<meta charset="UTF-8">
<title>Bram Keystone Homes — Business Card</title>
<link rel="stylesheet" href="https://fonts.googleapis.com/css2?family=Arimo:wght@700&family=Work+Sans:wght@400;500;800&display=swap">
<style>
  :root {
    --stage: #1f1f1f;
    --card-brown: #663300;
    --card-brown-light: #74482a;
    --ink: #ffffff;
  }
  * { box-sizing: border-box; margin: 0; padding: 0; }
  html, body {
    width: 1200px;
    height: 900px;
    overflow: hidden;
    background: var(--stage);
  }
  .canvas {
    width: 1200px;
    height: 900px;
    display: flex;
    flex-direction: column;
    align-items: center;
    justify-content: center;
    gap: 40px;
  }
  .card {
    position: relative;
    width: 700px;
    height: 400px;
    background: linear-gradient(200deg, var(--card-brown-light) 0%, var(--card-brown) 55%, #633314 100%);
    color: var(--ink);
  }
  .brand {
    display: flex;
    flex-direction: column;
    align-items: center;
  }
  .brand-name {
    font-family: "Work Sans", sans-serif;
    font-weight: 800;
    letter-spacing: -0.5px;
    line-height: 1;
    white-space: nowrap;
  }
  .brand-tagline {
    font-family: "Arimo", sans-serif;
    font-weight: 700;
    text-transform: uppercase;
    white-space: nowrap;
    margin-top: 4px;
  }

  /* Front */
  .card-front {
    display: flex;
    align-items: center;
    justify-content: center;
  }
  .card-front .brand-name { font-size: 44px; }
  .card-front .brand-tagline { font-size: 15.5px; letter-spacing: 0.3px; }

  /* Back */
  .card-back {
    display: flex;
    align-items: center;
  }
  .card-back .brand {
    width: 410px;
    padding-left: 20px;
  }
  .card-back .brand-name { font-size: 33px; }
  .card-back .brand-tagline { font-size: 11.5px; }
  .divider {
    width: 2px;
    height: 190px;
    background: var(--ink);
    margin-top: 40px;
  }
  .contact {
    padding-left: 28px;
    font-family: "Work Sans", sans-serif;
    margin-top: 40px;
  }
  .contact-name { font-size: 23px; font-weight: 500; line-height: 1.1; }
  .contact-role { font-size: 17px; font-weight: 400; margin-bottom: 14px; }
  .contact-address { font-size: 17px; line-height: 1.3; margin-bottom: 10px; }
  .contact-list { list-style: none; font-size: 17px; line-height: 1.5; }
  .contact-list li { display: flex; align-items: center; gap: 10px; }
  .contact-list svg { width: 13px; height: 13px; flex: none; }
</style>
</head>
<body>
<main class="canvas">
  <section class="card card-front">
    <div class="brand">
      <span class="brand-name">Bram Keystone Homes</span>
      <span class="brand-tagline">- Home Renovations - Custom Project Design -</span>
    </div>
  </section>

  <section class="card card-back">
    <div class="brand">
      <span class="brand-name">Bram Keystone Homes</span>
      <span class="brand-tagline">- Home Renovations - Custom Project Design -</span>
    </div>
    <div class="divider"></div>
    <div class="contact">
      <p class="contact-name">Ludovic Entrasse</p>
      <p class="contact-role">President / Ceo</p>
      <p class="contact-address">2718 Harlow Street<br>Marlow, AL 36540</p>
      <ul class="contact-list">
        <li>
          <svg viewBox="0 0 16 16" aria-hidden="true"><path d="M4 1.5l2.2 3-1.3 1.6c.9 1.9 2.4 3.4 4.3 4.3l1.6-1.3 3 2.2-1.2 2.4C7.300 13 3 8.700 1.600 3z" fill="none" stroke="#fff" stroke-width="1.4" stroke-linejoin="round"/></svg>
          <span>519.604.3087</span>
        </li>
        <li>
          <svg viewBox="0 0 16 16" aria-hidden="true"><rect x="1.5" y="3.5" width="13" height="9" fill="none" stroke="#fff" stroke-width="1.4"/><path d="M1.5 3.5L8 9l6.5-5.5" fill="none" stroke="#fff" stroke-width="1.4"/></svg>
          <span>info@bramkeystone.com</span>
        </li>
        <li>
          <svg viewBox="0 0 16 16" aria-hidden="true"><circle cx="8" cy="8" r="6.5" fill="none" stroke="#fff" stroke-width="1.3"/><ellipse cx="8" cy="8" rx="3" ry="6.5" fill="none" stroke="#fff" stroke-width="1.1"/><path d="M1.5 8h13M2.500 4.800h11M2.500 11.200h11" stroke="#fff" stroke-width="1.1"/></svg>
          <span>www.bramkeystone.com</span>
        </li>
      </ul>
    </div>
  </section>
</main>
</body>
</html>
```